Dental Practice Website design

Design a new website for Brambleford Dental Practice.
Design should be warm, neutral in colour, with some small amount of bright colour if needed but kept to a minimum. Website should look professional, high end. Home page should be easy to navigate and simple for patients to be able to book online.
Logo in files along with some examples of websites that we like. Please ask if any further info needed.
Menu should have:
About
New Patients
Treatments
Fees
Contact Us

Industry/Entity Type

Dentistry

Number of Pages Required

4 page

Font styles to use
Sans Serif

Colors

Designer to choose colors to be used in the design.

Requirements
Must have
• Ravelle ratings badge, book online button,
Nice to have
• neutral, relaxing colours
Should not have
• harsh, bright colours!

```html
<!DOCTYPE html>
<html lang="en">
<head>
<meta charset="utf-8">
<title>Brambleford Dental Practice</title>
<link rel="stylesheet" href="https://fonts.googleapis.com/css2?family=Poiret+One&family=Josefin+Sans:wght@300;400;600&family=Lato:wght@400;700&display=swap">
<style>
:root{
  --navy:#1b252d;
  --tan:#8c6f4b;
  --beige:#ede7dc;
  --ink:#2f3337;
  --muted:#6b6b6b;
  --line:#cfcac2;
  --white:#ffffff;
  --star:#e8611d;
}
*{box-sizing:border-box;margin:0;padding:0}
html,body{width:1200px;height:4570px;overflow:hidden}
body{position:relative;background:var(--white);font-family:"Josefin Sans",sans-serif;color:var(--ink)}
.abs{position:absolute}
.display{font-family:"Poiret One",sans-serif;font-weight:400;letter-spacing:1px;color:var(--ink)}
.btn{position:absolute;display:flex;align-items:center;justify-content:center;background:var(--navy);color:var(--white);font-size:14px;letter-spacing:.5px;border-radius:0 10px 0 10px;text-transform:uppercase}
.ph{position:absolute}
.social{position:absolute;display:flex;gap:8px}
.social span{width:26px;height:26px;border:2px solid currentColor;border-radius:50%}
/* header */
.nav a{position:absolute;top:98px;font-size:13px;color:var(--ink);text-decoration:none;letter-spacing:.4px}
.nav .active{border-bottom:1.5px solid var(--ink);padding-bottom:7px}
.logo{position:absolute;text-align:center;font-family:"Poiret One",sans-serif;line-height:1}
/* section heading */
.sec-title{position:absolute;left:0;width:1200px;text-align:center;font-size:31px}
.rule{position:absolute;height:1px;background:var(--line)}
.rule-strong{position:absolute;height:4px;background:var(--tan)}
/* service cards */
.card{position:absolute;top:1610px;width:312px;height:383px;background:var(--white);border-radius:22px;padding:7px}
.card .ph{left:7px;top:7px;width:298px;height:192px;border-radius:18px}
.card .icon{position:absolute;left:52px;top:166px;width:56px;height:56px;border-radius:50%;border:3px solid var(--white);background:var(--tan)}
.card h3{position:absolute;left:22px;top:246px;font-family:"Poiret One",sans-serif;font-size:25px;font-weight:400;color:var(--ink);white-space:nowrap}
.card p{position:absolute;left:22px;top:287px;width:280px;font-family:Lato,sans-serif;font-size:14px;line-height:20px;color:var(--muted)}
.card .more{position:absolute;left:28px;top:343px;font-family:Lato,sans-serif;font-size:13px;font-style:italic;text-decoration:underline;color:var(--ink)}
.arrow{position:absolute;width:42px;height:42px;border-radius:50%;background:var(--navy);display:flex;align-items:center;justify-content:center}
/* reviews */
.review{position:absolute;top:3002px;width:478px;height:292px;background:var(--white);border-radius:60px 0 130px 0}
.review .stars{position:absolute;left:52px;top:38px;color:var(--star);font-size:19px;letter-spacing:5px}
.review .badge{position:absolute;right:50px;top:32px;width:32px;height:32px;border-radius:50%;border:3px solid var(--tan)}
.review p{position:absolute;left:52px;top:78px;width:390px;font-family:Lato,sans-serif;font-size:15px;line-height:26px;color:var(--ink)}
.review .read{position:absolute;left:52px;top:154px;font-size:13px;color:var(--ink);letter-spacing:.3px}
.review .sep{position:absolute;left:52px;right:30px;top:186px;height:1px;background:var(--line)}
.review .avatar{position:absolute;left:57px;top:204px;width:60px;height:60px;border-radius:50%;background:linear-gradient(#9fb3c4,#5d6e7c)}
.review .name{position:absolute;left:131px;top:208px;font-size:21px;color:var(--ink)}
.review .date{position:absolute;left:131px;top:238px;font-size:11px;color:var(--ink)}
/* team */
.member{position:absolute;top:3680px;width:238px}
.member .ph{position:relative;width:238px;height:248px}
.member .who{margin:24px 0 0 18px;border-left:2px solid var(--line);padding-left:12px}
.member h4{font-family:Lato,sans-serif;font-weight:700;font-size:16px;color:var(--ink)}
.member small{display:block;margin-top:7px;font-family:Lato,sans-serif;font-weight:700;font-size:11px;color:var(--ink)}
/* footer */
.footer{position:absolute;left:0;top:4091px;width:1200px;height:479px;background:var(--navy);color:var(--white)}
.fcol{position:absolute;top:102px}
.fcol h5{font-family:Lato,sans-serif;font-weight:700;font-size:20px;margin-bottom:20px}
.fcol a{display:block;font-size:14px;color:#d9d9d9;text-decoration:none;letter-spacing:.5px;line-height:36.8px;text-transform:uppercase}
</style>
</head>
<body>

<!-- Header -->
<header>
  <div class="social" style="left:114px;top:29px;color:var(--ink)"><span></span><span></span><span></span><span></span><span></span></div>
  <div class="btn" style="left:910px;top:22px;width:178px;height:43px">Book Online</div>
  <div class="rule" style="left:114px;top:80px;width:974px;background:#e3e0db"></div>
  <nav class="nav">
    <a class="active" style="left:114px">HOME</a>
    <a style="left:208px">ABOUT</a>
    <a style="left:309px">NEW PATIENTS</a>
    <a style="left:773px">TREATMENTS</a>
    <a style="left:913px">FEES</a>
    <a style="left:1000px">CONTACT US</a>
  </nav>
  <div class="logo" style="left:450px;top:72px;width:300px">
    <div style="font-size:27px;color:#4a4a4a;letter-spacing:1px">BRAMBLEFORD</div>
    <div style="font-size:16px;color:var(--tan);margin-top:4px;letter-spacing:1px">DENTAL PRACTICE</div>
  </div>
</header>

<!-- Hero -->
<section class="hero">
  <div class="ph" role="img" aria-label="Smiling dental team in white coats reviewing notes in a bright clinic" style="left:0;top:153px;width:1200px;height:568px;background:linear-gradient(90deg,#f1f1f0 0%,#e9ebec 35%,#c9cfd4 60%,#aeb7be 100%)"></div>
  <div class="abs" style="left:32px;top:318px;transform:rotate(-90deg) translateX(-100%);transform-origin:left top;font-size:14px;color:var(--ink)">Scroll</div>
  <div class="abs" style="left:44px;top:390px;width:12px;height:12px;border-radius:50%;background:var(--navy)"></div>
  <div class="abs" style="left:44px;top:417px;width:12px;height:12px;border-radius:50%;background:#c8c8c8"></div>
  <div class="abs" style="left:44px;top:444px;width:12px;height:12px;border-radius:50%;background:#c8c8c8"></div>
  <div class="abs" style="left:44px;top:471px;width:12px;height:12px;border-radius:50%;background:#c8c8c8"></div>
  <h1 class="display abs" style="left:108px;top:312px;font-size:58px;line-height:60px;color:var(--navy)">BRAMBLEFORD<br>DENTAL PRACTICE</h1>
  <p class="abs" style="left:110px;top:450px;width:460px;font-size:15px;line-height:20px;color:var(--ink)">At our practice, we believe that a visit to the dentist should be a comfortable and positive experience.</p>
  <div class="btn" style="left:112px;top:515px;width:179px;height:40px">Our Treatments</div>
</section>

<!-- Introduction -->
<section class="intro">
  <div class="ph" role="img" aria-label="Two smiling dental professionals in white coats" style="left:114px;top:808px;width:482px;height:481px;border-radius:40px 40px 90px 40px;background:linear-gradient(135deg,#d7dde2,#a8b5bf)"></div>
  <div class="ph" role="img" aria-label="Modern dental treatment chair in a bright surgery" style="left:57px;top:1102px;width:227px;height:235px;border-radius:70px 0 110px 0;background:linear-gradient(135deg,#9fb4bf,#3f5763);border:0"></div>
  <h2 class="display abs" style="left:659px;top:822px;font-size:32px">INTRODUCTION</h2>
  <div class="rule" style="left:659px;top:874px;width:314px"></div>
  <div class="rule-strong" style="left:659px;top:872px;width:96px"></div>
  <p class="abs" style="left:659px;top:906px;width:410px;font-size:15px;line-height:30px;color:var(--ink)">Welcome to our friendly dental practice nestled in the heart of beautiful Ashcombe, UK. Our team of dedicated dentists, hygienists and support staff are here to provide you with exceptional dental care. With a wide array of services, including general and cosmetic dentistry, orthodontics and emergency care, we're confident that we can deliver the highest quality treatment to you and your loved ones.</p>
  <div class="btn" style="left:661px;top:1193px;width:177px;height:41px">Read More</div>
</section>

<!-- Services -->
<section class="services">
  <div class="abs" style="left:0;top:1422px;width:1200px;height:660px;background:var(--beige)"></div>
  <h2 class="display sec-title" style="top:1508px">EXPLORE OUR SERVICES</h2>
  <div class="rule" style="left:431px;top:1558px;width:336px"></div>
  <div class="rule-strong" style="left:552px;top:1556px;width:96px"></div>

  <div class="card" style="left:-240px;opacity:.45"><div class="ph" role="img" aria-label="Dental treatment photo" style="background:linear-gradient(135deg,#c9d4dc,#8ea3b1)"></div><h3>EMERGENCY DENTISTRY</h3><p>Duis aute irure dolor in reprehenderit</p></div>
  <div class="card" style="left:114px">
    <div class="ph" role="img" aria-label="Patient smiling during a dental check-up" style="background:linear-gradient(135deg,#8fb6d3,#d9c2b4)"></div>
    <div class="icon"></div>
    <h3>GENERAL DENTISTRY</h3>
    <p>Duis aute irure dolor in reprehenderit in voluptate Duis aute irure</p>
    <span class="more">VIEW MORE</span>
  </div>
  <div class="card" style="left:445px;border:1.5px dashed #555">
    <div class="ph" role="img" aria-label="Patient in a dental chair admiring her smile in a mirror" style="background:linear-gradient(135deg,#cfe0ea,#7fa6c4)"></div>
    <div class="icon" style="background:var(--navy)"></div>
    <h3>COSMETIC DENTISTRY</h3>
    <p>Duis aute irure dolor in reprehenderit in voluptate Duis aute irure</p>
    <span class="more">VIEW MORE</span>
  </div>
  <div class="card" style="left:779px">
    <div class="ph" role="img" aria-label="Dentist examining a smiling patient's teeth" style="background:linear-gradient(135deg,#5f6670,#d3b9ad)"></div>
    <div class="icon"></div>
    <h3>ORTHODONTICS</h3>
    <p>Duis aute irure dolor in reprehenderit in voluptate Duis aute irure</p>
    <span class="more">VIEW MORE</span>
  </div>
  <div class="card" style="left:1115px;opacity:.45"><div class="ph" role="img" aria-label="Dental treatment photo" style="background:linear-gradient(135deg,#d7d9dc,#a9b2ba)"></div><div class="icon" style="background:#cfcfcf"></div><h3>EMERGENCY</h3><p>Duis aute irure dolor in voluptate</p><span class="more">VIEW MORE</span></div>

  <div class="arrow" style="left:45px;top:1781px"><svg width="16" height="12" viewBox="0 0 16 12"><path d="M15 6H2M6 1L1 6l5 5" stroke="#fff" stroke-width="2" fill="none"/></svg></div>
  <div class="arrow" style="left:1110px;top:1781px"><svg width="16" height="12" viewBox="0 0 16 12"><path d="M1 6h13M10 1l5 5-5 5" stroke="#fff" stroke-width="2" fill="none"/></svg></div>
</section>

<!-- Join -->
<section class="join">
  <h2 class="display abs" style="left:115px;top:2201px;font-size:31px;color:var(--tan)">JOIN OUR PRACTICE</h2>
  <div class="rule" style="left:115px;top:2259px;width:316px"></div>
  <div class="abs" style="left:115px;top:2257px;width:95px;height:4px;background:var(--navy)"></div>
  <p class="abs" style="left:114px;top:2305px;width:460px;font-size:15px;line-height:25.7px;color:var(--ink)">If you're looking for an exceptional dental practice, we're here to help! Our team is made up of highly skilled professionals who are dedicated to ensuring that all our patients receive top-notch care in a welcoming and comfortable environment. Whether you need a routine examination or a more specialised treatment, we have all the resources to provide you with the best dental care possible. Our practice is always up-to-date with the latest techniques and technologies to make sure that our patients receive the best possible results. We understand that dental care can be expensive which is why we offer</p>
  <div class="btn" style="left:115px;top:2618px;width:223px;height:43px">More Information</div>
  <div class="ph" role="img" aria-label="Smiling dental nurse in blue scrubs" style="left:602px;top:2176px;width:483px;height:481px;border-radius:40px 40px 40px 90px;background:linear-gradient(135deg,#c9d3d9,#8fa2ae)"></div>
  <div class="ph" role="img" aria-label="Dentist treating a young child in the dental chair" style="left:914px;top:2471px;width:226px;height:232px;border-radius:0 40px 0 0;border:2px dashed #333;background:linear-gradient(135deg,#d6e4ea,#8ab8c9)"></div>
</section>

<!-- Reviews -->
<section class="reviews">
  <div class="abs" style="left:0;top:2801px;width:1200px;height:662px;background:var(--beige)"></div>
  <h2 class="display sec-title" style="top:2887px">RAVELLE RATINGS BADGE</h2>
  <div class="rule" style="left:419px;top:2937px;width:362px"></div>
  <div class="rule-strong" style="left:552px;top:2935px;width:96px"></div>

  <div class="review" style="left:105px">
    <div class="stars">★★★★★</div><div class="badge"></div>
    <p>Duis aute irure dolor in reprehenderit in voluptate velit esse cillum dolore eu fugiat nulla pariatur.</p>
    <div class="read">READ FULL REVIEW &nbsp;●</div><div class="sep"></div>
    <div class="avatar" role="img" aria-label="Reviewer portrait"></div>
    <div class="name">Owen Harlow</div><div class="date">10/3/2024</div>
  </div>
  <div class="review" style="left:614px">
    <div class="stars">★★★★★</div><div class="badge"></div>
    <p>Duis aute irure dolor in reprehenderit in voluptate velit esse cillum dolore eu fugiat nulla pariatur.</p>
    <div class="read">READ FULL REVIEW &nbsp;●</div><div class="sep"></div>
    <div class="avatar" role="img" aria-label="Reviewer portrait" style="background:linear-gradient(#c9b9ad,#7e8c96)"></div>
    <div class="name">Nina Castell</div><div class="date">10/3/2024</div>
  </div>

  <div class="arrow" style="left:548px;top:3331px;width:40px;height:40px"><svg width="16" height="12" viewBox="0 0 16 12"><path d="M15 6H2M6 1L1 6l5 5" stroke="#fff" stroke-width="2" fill="none"/></svg></div>
  <div class="arrow" style="left:610px;top:3331px;width:40px;height:40px;background:#a9a9a6"><svg width="16" height="12" viewBox="0 0 16 12"><path d="M1 6h13M10 1l5 5-5 5" stroke="#fff" stroke-width="2" fill="none"/></svg></div>
</section>

<!-- Team -->
<section class="team">
  <h2 class="display sec-title" style="top:3588px">OUR TEAM</h2>
  <div class="rule" style="left:457px;top:3638px;width:286px"></div>
  <div class="rule-strong" style="left:552px;top:3636px;width:96px"></div>

  <div class="member" style="left:114px">
    <div class="ph" role="img" aria-label="Portrait of a dentist in a white coat" style="background:linear-gradient(#4a4d4f,#2b2d2e)">
      <div class="abs" style="left:46px;top:117px;width:135px;height:32px;background:var(--tan);color:#f3ede4;font-size:13px;display:flex;align-items:center;justify-content:center">CONTACT</div>
    </div>
    <div class="who"><h4>Dr. Lena Marsh</h4><small>Dentist</small></div>
  </div>
  <div class="member" style="left:360px">
    <div class="ph" role="img" aria-label="Portrait of a dentist with arms crossed" style="background:linear-gradient(135deg,#dfe6ec,#9fb2c2)"></div>
    <div class="who"><h4>Dr. Theo Brandt</h4><small>Dentist</small></div>
  </div>
  <div class="member" style="left:607px">
    <div class="ph" role="img" aria-label="Portrait of a dentist in scrubs and gloves" style="background:linear-gradient(135deg,#e4e8ec,#8ea8c0)"></div>
    <div class="who"><h4>Dr. Ivy Pemberton</h4><small>Dentist</small></div>
  </div>
  <div class="member" style="left:854px">
    <div class="ph" role="img" aria-label="Portrait of a smiling dentist in a white coat" style="background:linear-gradient(135deg,#e8ecef,#b7c3cc)"></div>
    <div class="who"><h4>Dr. Rowan Kestrel</h4><small>Dentist</small></div>
  </div>
</section>

<!-- Footer -->
<footer class="footer">
  <div class="logo" style="left:104px;top:178px;width:230px;color:#e6e6e6">
    <div style="font-size:40px;letter-spacing:1px">BRAMBLEFORD</div>
    <div style="font-size:22px;margin-top:8px;letter-spacing:1px">DENTAL PRACTICE</div>
  </div>
  <div class="social" style="left:118px;top:284px;color:#e6e6e6"><span style="width:34px;height:34px"></span><span style="width:34px;height:34px"></span><span style="width:34px;height:34px"></span><span style="width:34px;height:34px"></span><span style="width:34px;height:34px"></span></div>
  <div class="fcol" style="left:426px"><h5>Quick Links</h5><a>About</a><a>New Patients</a><a>Treatments</a><a>Fees</a><a>Contact Us</a></div>
  <div class="fcol" style="left:662px"><h5>Terms &amp; Conditions</h5><a>Privacy Policy</a><a>Complaints</a><a>Procedure</a><a>Terms of Use</a><a>Health + Safety</a></div>
  <div class="fcol" style="left:935px"><h5>Contact Us</h5></div>
  <div class="abs" style="left:935px;top:134px;width:153px;height:39px;background:var(--tan);color:#e9dfd0;font-size:14px;display:flex;align-items:center;justify-content:center">BOOK ONLINE</div>
  <div class="abs" style="left:935px;top:196px;width:153px;height:39px;border:1px solid #cfd2d4;font-size:14px;display:flex;align-items:center;justify-content:center">+1 555-014-2280</div>
  <div class="abs" style="left:0;top:382px;width:1200px;text-align:center;font-size:15px">Copyrights 2025 Company Name All Rights Reserved</div>
</footer>

</body>
</html>
```